Redesign of business card for Cedar Ridge Mechanical

We are looking for a new design for our business cards for Cedar Ridge Mechanical. We are a plumbing & HVAC construction company, operating on the West Coast of Canada and USA. Logo attached.
Industry/Entity Type
Construction - Plumbing & HVAC
Contact Information for Business Card
Name, address, phone numbers, email, website address
Look and feel
Each slider illustrates characteristics of the customer's brand and the style your logo design should communicate.

```html
<!DOCTYPE html>
<html lang="en">
<head>
<meta charset="utf-8">
<title>Cedar Ridge Mechanical — Business Card</title>
<link rel="stylesheet" href="https://fonts.googleapis.com/css2?family=Montserrat:wght@400;600;700&display=swap">
<style>
  :root {
    --canvas: #d9d9d9;
    --card-black: #0d0d0d;
    --emboss: #262626;
    --panel-grey: #8a8c8e;
    --white: #ffffff;
    --ink: #111111;
    --soft-white: #e6e6e6;
  }
  * { margin: 0; padding: 0; box-sizing: border-box; }
  html, body {
    width: 1200px; height: 913px; overflow: hidden;
    background: var(--canvas);
    font-family: "Montserrat", sans-serif;
  }
  .stage { position: relative; width: 1200px; height: 913px; }

  .card {
    position: absolute;
    width: 600px; height: 345px;
    border-radius: 22px;
    overflow: hidden;
  }

  /* Back side */
  .card-back {
    left: 70px; top: 80px;
    background: var(--card-black);
    display: flex; align-items: center; justify-content: center; gap: 18px;
  }
  .card-back .brand-mark {
    width: 40px; height: 40px;
    border: 6px solid var(--emboss);
  }
  .card-back .brand-name {
    color: var(--emboss);
    font-weight: 700; font-size: 30px;
    text-transform: uppercase; letter-spacing: 1px;
  }

  /* Front side */
  .card-front { left: 530px; top: 480px; background: var(--white); }
  .card-front .shapes { position: absolute; inset: 0; }

  .identity { position: absolute; left: 30px; top: 38px; color: var(--white); }
  .identity .person-name { font-weight: 700; font-size: 22px; letter-spacing: 1px; }
  .identity .person-role { font-weight: 400; font-size: 15px; margin-top: 4px; color: var(--soft-white); }

  .front-brand {
    position: absolute; right: 28px; top: 60px;
    display: flex; align-items: center; gap: 12px;
  }
  .front-brand .brand-mark { width: 30px; height: 30px; border: 5px solid var(--ink); }
  .front-brand .brand-name {
    color: var(--ink); font-weight: 700; font-size: 21px;
    text-transform: uppercase; letter-spacing: 0.5px; line-height: 1.2;
  }

  .contact {
    position: absolute; left: 30px; top: 215px;
    color: var(--white); font-size: 15px; line-height: 1.45;
  }
  .contact .address { margin-bottom: 6px; }
  .contact .row { display: flex; align-items: center; gap: 10px; }
  .contact svg { width: 14px; height: 14px; flex: none; }
</style>
</head>
<body>
<main class="stage">

  <section class="card card-back" aria-label="Business card back">
    <span class="brand-mark"></span>
    <span class="brand-name">Cedar Ridge Mechanical</span>
  </section>

  <section class="card card-front" aria-label="Business card front">
    <svg class="shapes" viewBox="0 0 600 345" width="600" height="345" aria-hidden="true">
      <path d="M0,0 H250 C310,0 300,160 385,168 L0,178 Z" fill="var(--panel-grey)"/>
      <path d="M0,196 L380,188 C470,180 520,176 600,180 V345 H0 Z" fill="var(--card-black)"/>
    </svg>

    <div class="identity">
      <div class="person-name">DANIEL HAYES</div>
      <div class="person-role">Managing Director</div>
    </div>

    <div class="front-brand">
      <span class="brand-mark"></span>
      <span class="brand-name">Cedar Ridge<br>Mechanical</span>
    </div>

    <div class="contact">
      <div class="address">Your address, City<br>State, Zip 1234</div>
      <div class="row">
        <svg viewBox="0 0 16 16"><path d="M4 1 L6.5 4 L5 6 C6 8.5 7.5 10 10 11 L12 9.5 L15 12 L13 15 C7 14.5 1.5 9 1 3 Z" fill="#fff"/></svg>
        <span>123 456 789</span>
      </div>
      <div class="row">
        <svg viewBox="0 0 16 16"><rect x="1" y="3" width="14" height="10" fill="none" stroke="#fff" stroke-width="1.6"/><path d="M1 3 L8 9 L15 3" fill="none" stroke="#fff" stroke-width="1.6"/></svg>
        <span>info@yourgmail.com</span>
      </div>
      <div class="row">
        <svg viewBox="0 0 16 16"><circle cx="8" cy="8" r="6.5" fill="none" stroke="#fff" stroke-width="1.6"/><path d="M1.5 8 H14.5 M8 1.5 C5 5 5 11 8 14.5 M8 1.5 C11 5 11 11 8 14.5" fill="none" stroke="#fff" stroke-width="1.2"/></svg>
        <span>www.yourwebsite.com</span>
      </div>
    </div>
  </section>

</main>
</body>
</html>
```